BWP Business Card

A double sided business card based on your "Brindlewood Partners Ltd" Logo. To use the "BWP" logo on 1 side and the full company logo on the reverse.

Detials to be included:

Name: Tomas Wheeler
Postion: Consultant Orthotist & Expert Witness
T: +44 (0) 7700 938271
F: +44 (0) 7654 8820

```html
<!DOCTYPE html>
<html lang="en">
<head>
<meta charset="utf-8">
<title>BWP Business Card</title>
<link rel="stylesheet" href="https://fonts.googleapis.com/css2?family=Cinzel:wght@500;600&family=Open+Sans:wght@400;600;700&display=swap">
<style>
  :root {
    --navy: #0b3b6f;
    --grey: #9a9a9a;
    --grey-light: #c9c9c9;
    --paper: #ffffff;
    --stage: #e7e7ec;
    --ink-soft: #8c8c8c;
  }
  * { margin: 0; padding: 0; box-sizing: border-box; }
  html, body { width: 1200px; height: 987px; overflow: hidden; }
  body {
    background: var(--stage);
    font-family: "Open Sans", Arial, sans-serif;
    display: flex; flex-direction: column; align-items: center;
    justify-content: center; gap: 25px;
  }
  .card {
    width: 800px; height: 457px; border-radius: 34px;
    position: relative; overflow: hidden;
    box-shadow: 0 6px 18px rgba(0,0,0,0.12);
  }
  .card--back { background: var(--navy); display: flex; align-items: center; justify-content: center; gap: 22px; }
  .card--front { background: var(--paper); }
  .mark-square { width: 46px; height: 46px; background: var(--grey); }
  .back-name {
    font-family: "Cinzel", Georgia, serif; font-weight: 600;
    font-size: 96px; letter-spacing: 10px; color: var(--grey-light);
  }
  .swoosh { position: absolute; inset: 0; width: 100%; height: 100%; }
  .address { font-family: "Open Sans", Arial, sans-serif; font-size: 15px; fill: #fff; }
  .brand { position: absolute; left: 120px; top: 72px; display: flex; align-items: center; gap: 14px; }
  .brand .mark-square { background: var(--navy); width: 40px; height: 40px; }
  .brand-short { font-family: "Cinzel", Georgia, serif; font-weight: 600; font-size: 58px; letter-spacing: 6px; color: var(--navy); }
  .brand-divider { position: absolute; left: 372px; top: 52px; width: 1px; height: 130px; background: var(--grey-light); }
  .company { position: absolute; left: 394px; top: 60px; width: 380px; }
  .company-name {
    font-family: "Cinzel", Georgia, serif; font-weight: 600;
    font-size: 36px; line-height: 38px; color: var(--navy);
  }
  .company-tagline {
    margin-top: 8px; padding-top: 4px; padding-bottom: 6px;
    border-bottom: 1px solid var(--grey);
    font-family: "Cinzel", Georgia, serif; font-weight: 600;
    font-size: 12.5px; letter-spacing: 0.5px; color: var(--navy);
  }
  .person { position: absolute; right: 492px; top: 198px; text-align: right; }
  .person-name { font-weight: 700; font-size: 23px; color: var(--navy); }
  .person-role { font-size: 16px; line-height: 21px; color: var(--ink-soft); }
  .person-divider { position: absolute; left: 326px; top: 200px; width: 1px; height: 86px; background: var(--grey-light); }
  .contacts { position: absolute; left: 344px; top: 198px; list-style: none; }
  .contacts li { display: flex; align-items: center; gap: 10px; font-size: 18px; line-height: 30px; color: #4a4a4a; }
  .contacts svg { width: 18px; height: 18px; fill: var(--navy); }
</style>
</head>
<body>
  <section class="card card--back">
    <span class="mark-square"></span>
    <span class="back-name">BWP</span>
  </section>

  <section class="card card--front">
    <svg class="swoosh" viewBox="0 0 800 457" aria-hidden="true">
      <path d="M0,280 C160,282 270,335 370,400 C440,445 520,457 620,457 L0,457 Z" fill="var(--grey)"/>
      <path d="M0,296 C155,299 262,352 355,415 C415,452 480,457 540,457 L0,457 Z" fill="var(--paper)"/>
      <path d="M0,308 C150,312 252,364 342,426 C395,455 440,457 490,457 L0,457 Z" fill="var(--navy)"/>
      <path id="addressPath" d="M14,334 C140,340 240,388 330,452" fill="none"/>
      <text class="address"><textPath href="#addressPath">18 Halden Row, Kingsmere, Surrey, KT9 4QA</textPath></text>
    </svg>

    <div class="brand">
      <span class="mark-square"></span>
      <span class="brand-short">BWP</span>
    </div>
    <div class="brand-divider"></div>
    <div class="company">
      <div class="company-name">Brindlewood<br>Partners Ltd</div>
      <div class="company-tagline">Excellence in Medical Legal Reporting</div>
    </div>

    <div class="person">
      <div class="person-name">Tomas Wheeler</div>
      <div class="person-role">Consultant Orthotist</div>
      <div class="person-role">Expert Witness</div>
    </div>
    <div class="person-divider"></div>
    <ul class="contacts">
      <li>
        <svg viewBox="0 0 24 24" aria-label="Telephone"><path d="M6.6 10.8a15 15 0 0 0 6.6 6.6l2.2-2.2a1 1 0 0 1 1-.25 11.4 11.4 0 0 0 3.6.57 1 1 0 0 1 1 1V20a1 1 0 0 1-1 1A17 17 0 0 1 3 4a1 1 0 0 1 1-1h3.5a1 1 0 0 1 1 1c0 1.25.2 2.45.57 3.57a1 1 0 0 1-.25 1z"/></svg>
        +44 (0) 7700 938271
      </li>
      <li>
        <svg viewBox="0 0 24 24" aria-label="Fax"><path d="M6 2h9l3 3v4H6z M3 10h18a1 1 0 0 1 1 1v7h-4v4H6v-4H2v-7a1 1 0 0 1 1-1z M8 16v4h8v-4z"/></svg>
        +44 (0) 7654 8820
      </li>
      <li>
        <svg viewBox="0 0 24 24" aria-label="Email"><path d="M2 5h20v14H2z M4 7v.5l8 5.5 8-5.5V7z" fill-rule="evenodd"/></svg>
        tomas@brindlewoodpartners.co.uk
      </li>
    </ul>
  </section>
</body>
</html>
```